Corporate Business Card

Very professional, Modern, Not to busy, include phone address email, website
(480) 617-4930, 18761 52nd Avenue S, Mesa, AZ 85210, martin@plumlinegroup.com, varkoworks.com

Target Market(s)

Manufacturing

Industry/Entity Type

Aero, machining, manufacturing, Off road racing

Contact Information for Business Card

Phone, address email, website

```html
<!DOCTYPE html>
<html lang="en">
<head>
<meta charset="utf-8">
<title>Varko Works — Business Card</title>
<link rel="stylesheet" href="https://fonts.googleapis.com/css2?family=Saira:wght@700&family=Roboto:wght@400&display=swap">
<style>
  :root {
    --backdrop: #2e2e2f;
    --navy: #2b3a6e;
    --navy-deep: #23305c;
    --navy-light: #33447c;
    --white: #f1f1f3;
    --red: #d3222a;
    --rule: #d8d9de;
  }
  * { margin: 0; padding: 0; box-sizing: border-box; }
  html, body { width: 1200px; height: 1138px; overflow: hidden; }
  body { background: var(--backdrop); position: relative; font-family: "Roboto", sans-serif; }

  .card {
    position: absolute;
    border-radius: 16px;
    overflow: hidden;
    background: var(--navy);
  }
  .card-front { left: 274px; top: 186px; width: 623px; height: 376px; }
  .card-back  { left: 276px; top: 608px; width: 618px; height: 374px;
                background: linear-gradient(180deg, var(--navy) 0%, var(--navy-deep) 100%); }

  .emboss-pattern {
    position: absolute; inset: 0;
    background: linear-gradient(160deg, var(--navy-light) 0%, var(--navy) 50%, var(--navy-deep) 100%);
  }

  .brand-name {
    position: absolute;
    font-family: "Saira", sans-serif;
    font-weight: 700;
    color: var(--white);
    text-transform: uppercase;
    white-space: nowrap;
    line-height: 1;
  }
  .card-front .brand-name { left: 54px; top: 278px; font-size: 30px; letter-spacing: 1px; }
  .card-back .brand-name  { right: 34px; top: 78px; font-size: 39px; letter-spacing: 1px; }

  .holder-name {
    position: absolute; left: 34px; top: 256px;
    font-family: "Saira", sans-serif; font-weight: 700;
    font-size: 24px; line-height: 1; color: var(--white);
    text-transform: uppercase; letter-spacing: 0.5px;
  }
  .holder-name .surname { color: var(--red); }
  .name-rule {
    position: absolute; left: 248px; top: 275px;
    width: 334px; height: 2px; background: var(--rule);
  }

  .contact-line {
    position: absolute; left: 34px;
    display: flex; align-items: center; gap: 6px;
    font-size: 16px; color: var(--white); white-space: nowrap;
  }
  .contact-line.primary { top: 293px; }
  .contact-line.address { top: 316px; }
  .contact-item { display: inline-flex; align-items: center; gap: 9px; margin-right: 10px; }
  .contact-item svg { width: 14px; height: 14px; fill: var(--red); flex: none; }
</style>
</head>
<body>

  <section class="card card-front">
    <div class="emboss-pattern" role="img" aria-label="Tone-on-tone embossed repeating brand pattern in navy"></div>
    <div class="brand-name">Varko Works</div>
  </section>

  <section class="card card-back">
    <div class="brand-name">Varko Works</div>

    <div class="holder-name">Martin <span class="surname">Reyes</span></div>
    <div class="name-rule"></div>

    <div class="contact-line primary">
      <span class="contact-item">
        <svg viewBox="0 0 16 16" aria-hidden="true"><path d="M2 5c0-2 2-3 6-3s6 1 6 3v1h-3V4.5H5V6H2z M4 7h8l2 6H2z M8 8.5a2 2 0 1 0 0 4a2 2 0 0 0 0-4z"/></svg>
        (480) 617-4930
      </span>
      <span class="contact-item">
        <svg viewBox="0 0 16 16" aria-hidden="true"><path d="M1 3h14v10H1z M2 4l6 5 6-5v0.2L8 10 2 4.2z" fill-rule="evenodd"/></svg>
        martin@plumlinegroup.com
      </span>
      <span class="contact-item">
        <svg viewBox="0 0 16 16" aria-hidden="true"><path d="M8 1a7 7 0 1 0 0 14A7 7 0 0 0 8 1zm0 1.5c.9 0 1.9 1.8 2.2 4.5H5.8C6.1 4.3 7.1 2.5 8 2.5zM2.6 7h1.7c.1-1.6.5-3 1-4A5.5 5.5 0 0 0 2.6 7zm8.1 0h1.7a5.5 5.5 0 0 0-2.7-4c.5 1 .9 2.4 1 4zM2.6 9a5.5 5.5 0 0 0 2.7 4c-.5-1-.9-2.4-1-4zm3.2 0c.3 2.7 1.3 4.5 2.2 4.5s1.9-1.8 2.2-4.5zm4.9 0c-.1 1.6-.5 3-1 4a5.5 5.5 0 0 0 2.7-4z"/></svg>
        varkoworks.com
      </span>
    </div>

    <div class="contact-line address">
      <span class="contact-item">
        <svg viewBox="0 0 16 16" aria-hidden="true"><path d="M8 1a5 5 0 0 0-5 5c0 3.5 5 9 5 9s5-5.5 5-9a5 5 0 0 0-5-5zm0 3a2 2 0 1 1 0 4a2 2 0 0 1 0-4z" fill-rule="evenodd"/></svg>
        18761 52nd Avenue S, Mesa, AZ 85210
      </span>
    </div>
  </section>

</body>
</html>
```